Logo, Web and Mobile Designs for enterprise social media platform

All the details are in the attached document, please start reading the scope document first which explains what is this project about and the details about the needed deliverables, after that please read the UI_Requirements document which will detail what is expected regarding the coded web version since this is a coded contest, it is very important that you meet the UI requirements or suggest something else but we will need to agree first before working on the coded version

Good Luck

Target Market(s)

Enterprise Social Media

Industry/Entity Type

Media

Coding

Coded - Design and coding required

Number of Pages Required

5+ page

Font styles to use
Sans Serif

Requirements
Must have
• All the must haves are listed in the scope document so please check before you start

```html
<!DOCTYPE html>
<html lang="en">
<head>
<meta charset="utf-8">
<title>Teamora – Profile</title>
<link href="https://fonts.googleapis.com/css2?family=Roboto:ital,wght@0,400;0,500;0,700;1,400&display=swap" rel="stylesheet">
<style>
:root{
  --page:#ececec;
  --white:#ffffff;
  --panel-head:#f7f7f7;
  --border:#e2e2e2;
  --text:#555555;
  --heading:#444444;
  --muted:#666666;
  --blue:#1f8fc4;
  --blue-btn:#2196d3;
  --orange:#f29c11;
  --footer:#1f8ab8;
}
*{box-sizing:border-box;margin:0;padding:0}
html,body{width:873px;height:1200px;overflow:hidden}
body{background:var(--page);font-family:'Roboto',sans-serif;color:var(--text);position:relative}

.topbar{height:52px;background:linear-gradient(#fdfdfd,#f2f2f2);border-bottom:1px solid #dcdcdc;position:relative}
.menu-toggle{position:absolute;left:0;top:0;width:105px;height:52px;border-right:1px solid #e4e4e4}
.menu-toggle span{position:absolute;left:73px;width:14px;height:2px;background:#888}
.brand{position:absolute;left:122px;top:11px;display:flex;align-items:center;gap:6px}
.brand-dot{width:32px;height:32px;border-radius:50%;background:var(--orange)}
.brand-name{font-size:23px;font-weight:500;color:var(--blue)}
.user{position:absolute;left:542px;top:14px;display:flex;align-items:center;gap:9px;font-size:13px;color:#444}
.user-avatar{width:25px;height:25px;border-radius:50%;background:linear-gradient(#777,#333)}
.caret{width:0;height:0;border-left:4px solid transparent;border-right:4px solid transparent;border-top:5px solid #555;margin-left:4px}
.tool{position:absolute;top:0;height:52px;border-left:1px solid #e4e4e4;width:46px}
.badge{position:absolute;top:11px;min-width:14px;height:12px;border-radius:6px;color:#fff;font-size:8px;text-align:center;line-height:12px;padding:0 3px}

.panel{position:absolute;left:72px;width:728px;background:var(--white);border:1px solid var(--border)}
.panel-head{height:36px;background:var(--panel-head);border-bottom:1px solid var(--border);display:flex;align-items:center;justify-content:space-between;padding:0 8px 0 14px}
.panel-title{font-size:12px;color:var(--heading);text-transform:uppercase}

.btn-add{width:94px;height:24px;background:var(--blue-btn);color:#fff;font-size:9.5px;border-radius:2px;display:flex;align-items:center;justify-content:center;gap:4px;text-transform:uppercase}

.form-body{position:relative;height:246px}
.form-row{position:absolute;left:27px;font-size:11px;color:var(--muted)}
.field{position:absolute;left:133px;width:341px;border:1px solid #dcdcdc;background:#fff}
.btn-update{position:absolute;left:133px;top:204px;width:83px;height:24px;background:var(--orange);color:#fff;font-size:11.5px;font-weight:500;border-radius:2px;display:flex;align-items:center;justify-content:center;letter-spacing:.3px}
.decor{position:absolute;left:495px;top:30px;width:210px;height:180px;border-radius:50%;background:radial-gradient(#fffdf5,#fbfaf4 60%,#fff 75%)}

.member{position:relative;height:80px;border-bottom:1px solid #efefef}
.member:last-child{border-bottom:none}
.member-photo{position:absolute;left:19px;top:12px;width:53px;height:53px;border-radius:50%;background:radial-gradient(circle at 50% 40%,#d8b79a,#7a5a44)}
.member-name{position:absolute;left:86px;top:18px;font-size:9.5px;color:var(--blue);text-transform:uppercase}
.stars{position:absolute;left:141px;top:17px;font-size:9px;color:var(--orange);letter-spacing:-.5px}
.stars i{font-style:normal;color:#c9c9c9}
.member-text{position:absolute;left:86px;top:37px;font-size:8px;font-style:italic;line-height:14px;color:#444}
.member .btn-add{position:absolute;right:8px;top:24px}

.intro{padding:20px 38px 12px 29px}
.intro h2{font-size:11.5px;font-weight:400;color:#333;text-transform:uppercase;margin-bottom:9px}
.intro p{font-size:7.6px;line-height:15px;color:#555}

.footer{position:absolute;left:0;top:1092px;width:873px;height:108px;background:var(--footer);color:#fff;text-align:center}
.social{display:flex;justify-content:center;gap:9px;margin-top:20px}
.social span{width:18px;height:18px;border-radius:3px;background:#fff}
.footer-nav{margin-top:10px;font-size:10.5px}
.footer-nav span{margin:0 5px;opacity:.9}
.copyright{margin-top:9px;font-size:10px}
</style>
</head>
<body>
<header class="topbar">
  <div class="menu-toggle"><span style="top:21px"></span><span style="top:26px"></span><span style="top:31px"></span></div>
  <div class="brand"><div class="brand-dot"></div><div class="brand-name">Teamora</div></div>
  <div class="user"><div class="user-avatar" role="img" aria-label="User avatar"></div>Sam Carter<div class="caret"></div></div>
  <div class="tool" style="left:672px">
    <svg width="46" height="52"><rect x="16" y="20" width="14" height="3" fill="#888"/><rect x="16" y="25" width="14" height="3" fill="#888"/><rect x="16" y="30" width="14" height="3" fill="#888"/></svg>
    <div class="badge" style="left:21px;background:var(--orange)">8</div>
  </div>
  <div class="tool" style="left:718px">
    <svg width="46" height="52"><circle cx="24" cy="25" r="5" fill="none" stroke="#777" stroke-width="2"/><line x1="28" y1="29" x2="31" y2="32" stroke="#777" stroke-width="2.4"/></svg>
  </div>
  <div class="tool" style="left:764px">
    <svg width="46" height="52"><path d="M17 32 h12 l-2-3 v-5 a4 4 0 0 0-8 0 v5 z" fill="#777"/><circle cx="23" cy="33.5" r="1.6" fill="#777"/></svg>
    <div class="badge" style="left:21px;background:var(--blue-btn)">8</div>
  </div>
</header>

<section class="panel" style="top:81px;height:284px">
  <div class="panel-head"><span class="panel-title">Basic Informations</span>
    <svg width="10" height="10"><path d="M3 2 l4 3 -4 3" fill="none" stroke="#aaa" stroke-width="1.2"/></svg></div>
  <div class="form-body">
    <div class="decor" role="img" aria-label="Faint speech bubble decoration"></div>
    <div class="form-row" style="top:29px">Name : *</div>
    <div class="field" style="top:21px;height:29px"></div>
    <div class="form-row" style="top:66px">About : *</div>
    <div class="field" style="top:58px;height:29px"></div>
    <div class="form-row" style="top:106px">Description : *</div>
    <div class="field" style="top:98px;height:91px"></div>
    <div class="btn-update">UPDATE</div>
  </div>
</section>

<section class="panel" style="top:382px;height:273px">
  <div class="panel-head"><span class="panel-title">Groups Name</span><div class="btn-add">&#10010; Add Friends</div></div>
  <div class="member"><div class="member-photo" role="img" aria-label="Member portrait"></div><div class="member-name">John Doe</div><div class="stars">★★★<i>☆☆</i></div><div class="member-text">Lorem ipsum dolor sit amet,<br>consectetur adipiscing elit, sed do</div><div class="btn-add">&#10010; Add Friends</div></div>
  <div class="member"><div class="member-photo" role="img" aria-label="Member portrait"></div><div class="member-name">John Doe</div><div class="stars">★★★<i>☆☆</i></div><div class="member-text">Lorem ipsum dolor sit amet,<br>consectetur adipiscing elit, sed do</div><div class="btn-add">&#10010; Add Friends</div></div>
  <div class="member"><div class="member-photo" role="img" aria-label="Member portrait"></div><div class="member-name">John Doe</div><div class="stars">★★★<i>☆☆</i></div><div class="member-text">Lorem ipsum dolor sit amet,<br>consectetur adipiscing elit, sed do</div><div class="btn-add">&#10010; Add Friends</div></div>
</section>

<section class="panel" style="top:674px;height:385px">
  <div class="panel-head"><span class="panel-title">Bos Informations</span><div class="btn-add">&#10010; Add Friends</div></div>
  <div class="intro">
    <h2>Nemo enim ipsam voluptatem quia voluptas sit aspernatur aut odit aut</h2>
    <p>Lorem ipsum dolor sit amet, consectetur adipiscing elit, sed do eiusmod tempor incididunt ut labore et dolore magna aliqua. Ut enim ad minim veniam, quis nostrud exercitation ullamco laboris nisi ut aliquip ex ea commodo consequat. Duis aute irure dolor in reprehenderit in voluptate velit esse cillum dolore eu fugiat nulla pariatur. Excepteur sint occaecat cupidatat non proident, sunt in culpa qui officia deserunt mollit anim id est laborum.</p>
  </div>
  <div class="member"><div class="member-photo" role="img" aria-label="Member portrait"></div><div class="member-name">John Doe</div><div class="stars">★★★<i>☆☆</i></div><div class="member-text">Lorem ipsum dolor sit amet,<br>consectetur adipiscing elit, sed do</div><div class="btn-add">&#10010; Add Friends</div></div>
  <div class="member"><div class="member-photo" role="img" aria-label="Member portrait"></div><div class="member-name">John Doe</div><div class="stars">★★★<i>☆☆</i></div><div class="member-text">Lorem ipsum dolor sit amet,<br>consectetur adipiscing elit, sed do</div><div class="btn-add">&#10010; Add Friends</div></div>
  <div class="member"><div class="member-photo" role="img" aria-label="Member portrait"></div><div class="member-name">John Doe</div><div class="stars">★★★<i>☆☆</i></div><div class="member-text">Lorem ipsum dolor sit amet,<br>consectetur adipiscing elit, sed do</div><div class="btn-add">&#10010; Add Friends</div></div>
</section>

<footer class="footer">
  <div class="social"><span></span><span></span><span></span><span></span><span></span></div>
  <div class="footer-nav">Home <span>/</span> Contact <span>/</span> Topics <span>/</span> Posts and Comments <span>/</span> Discussion <span>/</span> Videos Links</div>
  <div class="copyright">Copyright @ 2015 - 2015.Teamora. All Rights Reserved.</div>
</footer>
</body>
</html>
```